Creative, Colorful, Dynamic Infographic for Global Non-Profit

We are a global arts and education non-profit in need of an infographic that illustrates four key skills embedded in our work: Curiosity, Listening, Imagination, Postive Action.
We work primarily with educators, students, and artists who use the power of personal stories to build community and connection and to bridge divides.
Our new brand guidelines, logos, and fonts are here: https://stylevault.example/lumen-circle
I've attached a mock-up of the graphic and the required text. (Note the attached design was created by a staff person, your final design does not need to be the same. The color scheme and text of the final design should match the brand guidelines above.)
The graphic will be used for both web and print media and should include the purple Lumen Circle logo (also attached).
Ideally the final design will delight audiences and spark interest in our work.

```html
<!DOCTYPE html>
<html lang="en">
<head>
<meta charset="utf-8">
<title>Lumen Circle – Four Skills</title>
<link rel="stylesheet" href="https://fonts.googleapis.com/css2?family=Work+Sans:wght@400;600&display=swap">
<style>
  :root {
    --purple: #643394;
    --red: #ee4343;
    --blue: #226bbf;
    --yellow: #e8ca48;
    --ink: #333333;
    --paper: #fdfdfd;
    --white: #ffffff;
  }
  html, body {
    margin: 0;
    padding: 0;
    width: 1200px;
    height: 1200px;
    overflow: hidden;
    background: var(--paper);
  }
  .skills-wheel {
    display: block;
    width: 1200px;
    height: 1200px;
    font-family: "Work Sans", Arial, sans-serif;
  }
  .arm--red, .quad--red { fill: var(--red); }
  .arm--purple, .quad--purple { fill: var(--purple); }
  .arm--blue, .quad--blue { fill: var(--blue); }
  .arm--yellow, .quad--yellow { fill: var(--yellow); }
  .ring-gap { fill: var(--white); }
  .ring { fill: var(--white); stroke-width: 31; }
  .ring--purple { stroke: var(--purple); }
  .ring--red { stroke: var(--red); }
  .ring--yellow { stroke: var(--yellow); }
  .ring--blue { stroke: var(--blue); }
  .badge--purple { fill: var(--purple); }
  .badge--red { fill: var(--red); }
  .badge--yellow { fill: var(--yellow); }
  .badge--blue { fill: var(--blue); }
  .arrow { fill: none; stroke: var(--white); stroke-width: 12; }
  .skill-text { fill: var(--ink); font-size: 35px; font-weight: 400; text-anchor: middle; }
  .skill-title { font-weight: 600; }
  .link-text { fill: var(--white); font-size: 30px; font-weight: 400; text-anchor: middle; }
  .link-text--dark { fill: var(--ink); }
  .hub { fill: var(--purple); stroke: var(--white); stroke-width: 7; }
  .hub-name { fill: var(--white); font-size: 34px; font-weight: 600; text-anchor: middle; }
</style>
</head>
<body>
<svg class="skills-wheel" viewBox="0 0 1932 1932" xmlns="http://www.w3.org/2000/svg" role="img" aria-label="Lumen Circle four skills cycle: Curiosity, Listening, Imagination, Positive action">
  <!-- arms -->
  <path class="arm--red" d="M932 232 H997 A175 175 0 0 0 1172 407 V757 H756 V407 A175 175 0 0 0 932 232 Z"/>
  <path class="arm--blue" d="M1700 932 V997 A175 175 0 0 0 1525 1172 H1172 V757 H1525 A175 175 0 0 0 1700 932 Z"/>
  <path class="arm--yellow" d="M997 1700 H932 A175 175 0 0 0 756 1525 V1172 H1172 V1525 A175 175 0 0 0 997 1700 Z"/>
  <path class="arm--purple" d="M228 997 V932 A175 175 0 0 0 403 757 H756 V1172 H403 A175 175 0 0 0 228 997 Z"/>
  <!-- centre quadrants -->
  <rect class="quad--purple" x="756" y="757" width="208" height="208"/>
  <rect class="quad--red" x="964" y="757" width="208" height="208"/>
  <rect class="quad--yellow" x="756" y="965" width="208" height="207"/>
  <rect class="quad--blue" x="964" y="965" width="208" height="207"/>

  <!-- link texts -->
  <text class="link-text" x="966" y="420"><tspan x="966">Your positive actions</tspan><tspan x="966" dy="42">lead to curiosity</tspan><tspan x="966" dy="42">about what else</tspan><tspan x="966" dy="42">is possible</tspan></text>
  <text class="link-text" x="466" y="934"><tspan x="466">Your curiosity</tspan><tspan x="466" dy="42">allows you</tspan><tspan x="466" dy="42">to listen</tspan></text>
  <text class="link-text" x="1486" y="934"><tspan x="1486">Your imagination</tspan><tspan x="1486" dy="42">can spark</tspan><tspan x="1486" dy="42">positive action</tspan></text>
  <text class="link-text link-text--dark" x="966" y="1434"><tspan x="966">Your listening</tspan><tspan x="966" dy="42">allows you to</tspan><tspan x="966" dy="42">take in new</tspan><tspan x="966" dy="42">information</tspan></text>

  <!-- skill rings -->
  <circle class="ring-gap" cx="698" cy="700" r="240"/>
  <circle class="ring-gap" cx="1230" cy="700" r="240"/>
  <circle class="ring-gap" cx="698" cy="1230" r="240"/>
  <circle class="ring-gap" cx="1230" cy="1230" r="240"/>
  <circle class="ring ring--purple" cx="698" cy="700" r="216"/>
  <circle class="ring ring--red" cx="1230" cy="700" r="216"/>
  <circle class="ring ring--yellow" cx="698" cy="1230" r="216"/>
  <circle class="ring ring--blue" cx="1230" cy="1230" r="216"/>

  <!-- skill texts -->
  <text class="skill-text" x="698" y="628"><tspan class="skill-title" x="698">Curiosity –</tspan><tspan x="698" dy="42">Focus on how you can</tspan><tspan x="698" dy="42">learn from another's</tspan><tspan x="698" dy="42">knowledge and</tspan><tspan x="698" dy="42">experience</tspan></text>
  <text class="skill-text" x="1240" y="628"><tspan class="skill-title" x="1240">Positive action -</tspan><tspan x="1240" dy="42">Show your words</tspan><tspan x="1240" dy="42">and actions</tspan><tspan x="1240" dy="42">matter</tspan></text>
  <text class="skill-text" x="696" y="1178"><tspan class="skill-title" x="696">Listening –</tspan><tspan x="696" dy="42">Seek to</tspan><tspan x="696" dy="42">understand</tspan><tspan x="696" dy="42">before speaking</tspan></text>
  <text class="skill-text" x="1230" y="1178"><tspan class="skill-title" x="1230">Imagination –</tspan><tspan x="1230" dy="42">Consider</tspan><tspan x="1230" dy="42">possibilities beyond</tspan><tspan x="1230" dy="42">what you know</tspan></text>

  <!-- arrow badges -->
  <rect class="badge--red" x="958" y="655" width="122" height="90" rx="18"/>
  <path class="arrow" d="M1052 700 H994 M1020 674 L994 700 L1020 726"/>
  <rect class="badge--purple" x="654" y="850" width="90" height="122" rx="18"/>
  <path class="arrow" d="M699 880 V938 M673 912 L699 938 L725 912"/>
  <rect class="badge--yellow" x="848" y="1184" width="122" height="90" rx="18"/>
  <path class="arrow" d="M877 1229 H937 M911 1203 L937 1229 L911 1255"/>
  <rect class="badge--blue" x="1186" y="958" width="90" height="122" rx="18"/>
  <path class="arrow" d="M1231 1052 V992 M1205 1018 L1231 992 L1257 1018"/>

  <!-- hub -->
  <circle class="hub" cx="963" cy="968" r="118"/>
  <text class="hub-name" x="963" y="960"><tspan x="963">Lumen</tspan><tspan x="963" dy="40">Circle</tspan></text>
</svg>
</body>
</html>
```